Business Card Design Project

Business Card
We are rebranding with a new logo
Industry/Entity Type
Business
Contact Information for Business Card
Dennis Morvale +61 487215963 dennis@quorv.com.au P.O. Box 872 Fernlow QLD 4309
Requirements
Must have
- Logo

```html
<!DOCTYPE html>
<html lang="en">
<head>
<meta charset="utf-8">
<title>Quorv International Business Card</title>
<link href="https://fonts.googleapis.com/css2?family=Roboto:wght@400;500&family=Roboto+Condensed:wght@700&display=swap" rel="stylesheet">
<style>
  :root {
    --backdrop: #262626;
    --card: #f2f2f2;
    --brand-blue: #1a8ac6;
    --deep-blue: #0b5e87;
    --bright-blue: #1a9bd8;
    --text-grey: #555555;
  }
  html, body {
    margin: 0;
    width: 1200px;
    height: 960px;
    overflow: hidden;
    background: var(--backdrop);
  }
  .card {
    position: absolute;
    left: 223px;
    top: 265px;
    width: 754px;
    height: 430px;
    background: var(--card);
    font-family: "Roboto", Arial, sans-serif;
    box-shadow: 0 4px 14px rgba(0,0,0,0.5);
    overflow: hidden;
  }
  .brand {
    position: absolute;
    left: 60px;
    top: 120px;
    display: flex;
    align-items: center;
    gap: 12px;
  }
  .brand-dot {
    width: 22px;
    height: 22px;
    border-radius: 50%;
    background: var(--brand-blue);
  }
  .brand-name {
    font-weight: 500;
    font-size: 34px;
    color: var(--brand-blue);
    letter-spacing: 1px;
  }
  .holder {
    position: absolute;
    left: 60px;
    top: 294px;
  }
  .holder-name {
    margin: 0 0 10px;
    font-family: "Roboto Condensed", "Arial Narrow", sans-serif;
    font-weight: 700;
    font-size: 25px;
    line-height: 30px;
    color: var(--brand-blue);
    letter-spacing: 0.2px;
  }
  .postal {
    font-style: normal;
    font-size: 18px;
    line-height: 23px;
    color: var(--text-grey);
  }
  .contact {
    position: absolute;
    left: 488px;
    top: 307px;
    margin: 0;
    padding: 0;
    list-style: none;
    font-size: 18px;
    line-height: 24px;
    color: var(--text-grey);
  }
  .contact li {
    display: flex;
    align-items: center;
    gap: 11px;
  }
  .contact svg { width: 16px; height: 16px; fill: var(--brand-blue); }
  .edge-band {
    position: absolute;
    right: 0;
    top: 0;
    width: 19px;
    height: 430px;
    background: linear-gradient(180deg, var(--deep-blue), var(--bright-blue));
  }
</style>
</head>
<body>
  <div class="card">
    <div class="brand">
      <span class="brand-dot"></span>
      <span class="brand-name">Quorv International</span>
    </div>

    <div class="holder">
      <h1 class="holder-name">DENNIS MORVALE</h1>
      <address class="postal">P.O. Box 872<br>Fernlow QLD 4309</address>
    </div>

    <ul class="contact">
      <li>
        <svg viewBox="0 0 16 16"><path d="M3.5 1.5l2.5 0 1 3.5-1.8 1.2a9 9 0 0 0 4.6 4.6L11 9l3.5 1v2.5c0 1-1 2-2 2A11.5 11.5 0 0 1 1.5 3.5c0-1 1-2 2-2z"/></svg>
        +61 487215963
      </li>
      <li>
        <svg viewBox="0 0 16 16"><path d="M1 3h14v1.2L8 9 1 4.2z"/><path d="M1 5.6l7 4.8 7-4.8V13H1z"/></svg>
        dennis@quorv.com.au
      </li>
      <li>
        <svg viewBox="0 0 16 16"><circle cx="8" cy="8" r="7"/><path d="M4 5c2 0 3 1 2.5 2.5S4 9 5 11M10 2.5c-1 2 1 3 3 3M11 10c1 1 0 3-1 3.5" stroke="#f2f2f2" stroke-width="1.3" fill="none"/></svg>
        www.quorv.com.au
      </li>
    </ul>

    <div class="edge-band" role="img" aria-label="Decorative brand colour strip along the right edge"></div>
  </div>
</body>
</html>
```